Business Card Design

Please use the Logo for colors and styles, and create a business card using the following info:

Lukas Brenner
Web Developer

Talvo Systems
+41 78 412 65 08
lukas@talvo-systems.ch
www.talvo-systems.ch

Download the logo at http://talvo-systems.ch/tl_files/talvo_systems.zip

Thanks for your works!

```html
<!DOCTYPE html>
<html lang="en">
<head>
<meta charset="utf-8">
<title>Talvo Systems – Business Card</title>
<link href="https://fonts.googleapis.com/css2?family=Jost:wght@400;500&display=swap" rel="stylesheet">
<style>
  :root {
    --bg: #e9ebee;
    --card-white: #ffffff;
    --navy: #0f4675;
    --sky: #0b7fd0;
    --tint-light: #eef5fb;
    --tint-mid: #d3e6f5;
    --ink: #1c3550;
    --shadow: rgba(20, 40, 70, 0.18);
  }
  * { box-sizing: border-box; margin: 0; padding: 0; }
  html, body {
    width: 1200px; height: 821px; overflow: hidden;
    background: var(--bg);
    font-family: "Jost", "Futura", sans-serif;
  }
  .sheet {
    position: relative; width: 1200px; height: 821px;
    display: flex; align-items: center; justify-content: center; gap: 40px;
  }
  .card {
    position: relative; width: 540px; height: 310px;
    border-radius: 14px; overflow: hidden;
    box-shadow: 0 10px 28px var(--shadow);
  }
  /* Front */
  .card--front { background: var(--card-white); }
  .card__ornament {
    position: absolute; top: 0; right: 0; width: 270px; height: 310px;
    background: linear-gradient(135deg, var(--tint-light), var(--tint-mid));
  }
  .brand {
    position: absolute; top: 34px; left: 32px;
    font-weight: 500; font-size: 26px; letter-spacing: 0.5px;
    color: var(--sky); text-transform: uppercase;
  }
  .person {
    position: absolute; right: 0; width: 270px; top: 128px;
    text-align: center;
  }
  .person__name { font-size: 25px; font-weight: 500; color: var(--sky); line-height: 1; }
  .person__role { font-size: 13px; color: var(--navy); margin-top: 4px; }
  .contact {
    position: absolute; left: 32px; bottom: 26px;
    font-size: 14px; line-height: 1.35; color: var(--ink);
  }
  .contact__company { font-weight: 500; }
  .contact__label { color: var(--sky); }
  .contact__web { font-weight: 500; }
  /* Back */
  .card--back {
    background: var(--navy);
    display: flex; align-items: center; justify-content: center;
  }
  .card--back .brand {
    position: static; font-size: 40px; color: #ffffff;
  }
  .back-web {
    position: absolute; bottom: 28px; left: 0; right: 0;
    text-align: center; font-size: 15px; color: #ffffff;
  }
  .back-web__part { color: var(--sky); }
</style>
</head>
<body>
<main class="sheet">
  <section class="card card--front" aria-label="Card front">
    <div class="card__ornament" role="img" aria-label="Decorative blue ring ornament framing the name"></div>
    <div class="brand">Talvo Systems</div>
    <div class="person">
      <div class="person__name">Lukas Brenner</div>
      <div class="person__role">Web Developer</div>
    </div>
    <div class="contact">
      <div class="contact__company">Talvo Systems</div>
      <div><span class="contact__label">P:</span> +41 78 412 65 08</div>
      <div><span class="contact__label">E:</span> lukas@talvo-systems.ch</div>
      <div class="contact__web">www.talvo-systems.ch</div>
    </div>
  </section>

  <section class="card card--back" aria-label="Card back">
    <div class="brand">Talvo Systems</div>
    <div class="back-web"><span class="back-web__part">www.</span>talvo-systems<span class="back-web__part">.ch</span></div>
  </section>
</main>
</body>
</html>
```